Summit Builders Web Site / Business Cards

Construction Company that specializes in Water and Fire Damage, Residential ReModels, Landscaping and Building ADU (Accessory Dwelling Unit)

Growing and changing families often need additional space, and a remodeling project can often provide that. Adding a new area, or repurposing an existing one can satisfy this requirement.

Other times, homeowners want to update the look in their kitchen or bathroom with more than just a change of cabinetry or vanity doors and drawers. Whatever your needs are, Summit Builders has skilled workers who are bonded and insured, and ready to make your dreams and visions a reality.

Target Market(s)

Home Owners

Industry/Entity Type

Construction Company

Contact Information for Business Card

Center Logo with our information on the corners

Back side to be Logo Only
Contact Info
CSLB License # 2418596
info@summitbuildersca.example
www.summitbuildersca.example

Coding

Coded - Design and coding required

Number of Pages Required

5+ page

Font styles to use
Serif
Sans Serif

Requirements
Must have
• Using our Logo Colors
Home
About Us
Services
Projects / Portfolio
Contact Us
Nice to have
• Colors matching our Logo
Should not have
• Black because it doesnt match our logo

```html
<!DOCTYPE html>
<html lang="en">
<head>
<meta charset="utf-8">
<title>Summit Builders</title>
<link href="https://fonts.googleapis.com/css2?family=Montserrat:wght@500;600;700;800&family=Roboto:ital,wght@0,400;0,500;1,400&display=swap" rel="stylesheet">
<style>
:root{
  --orange:#ef5a22;
  --orange-light:#f57a35;
  --orange-deep:#e0481a;
  --charcoal:#3b3d42;
  --slate:#4a4d55;
  --ink:#2b2b2e;
  --body:#55575c;
  --mist:#eef0f3;
  --white:#ffffff;
}
*{box-sizing:border-box;margin:0;padding:0}
html,body{width:1200px;height:4640px;overflow:hidden;background:var(--white)}
body{position:relative;font-family:'Roboto',sans-serif;color:var(--body)}
.abs{position:absolute}
.head-font{font-family:'Montserrat',sans-serif}

/* header */
.site-header{left:0;top:0;width:1200px;height:108px;background:var(--white)}
.brand{left:171px;top:22px;display:flex;align-items:center;gap:10px;font-family:'Montserrat',sans-serif;font-weight:700;font-size:20px;color:var(--ink);letter-spacing:1px}
.brand-mark{width:24px;height:24px;background:var(--orange)}
.license-top{left:537px;top:30px;font:600 16px 'Montserrat',sans-serif;color:var(--orange)}
.email-top{left:756px;top:28px;font:600 16px 'Montserrat',sans-serif;color:var(--orange);display:flex;align-items:center;gap:6px}
.main-nav a{position:absolute;top:78px;font:600 14px 'Montserrat',sans-serif;color:var(--ink);text-decoration:none}
.main-nav a.active{color:var(--orange)}

/* hero */
.hero{left:0;top:108px;width:1200px;height:600px}
.hero-title{left:500px;top:210px;width:560px;text-align:center;font:800 42px 'Montserrat',sans-serif;color:var(--white);letter-spacing:.5px}
.hero-sub{left:500px;top:258px;width:560px;text-align:center;font:600 31px 'Montserrat',sans-serif;color:var(--white)}
.btn{display:flex;align-items:center;justify-content:center;background:var(--orange);color:var(--white);font:700 13px 'Montserrat',sans-serif;border-radius:22px}
.hero-btn{left:713px;top:319px;width:134px;height:38px}

/* welcome */
.welcome-title{left:175px;top:822px;font:700 46px 'Montserrat',sans-serif;color:var(--ink)}
.welcome-text{left:171px;top:897px;width:362px;font-size:12.5px;line-height:22.4px;color:var(--body)}

/* specialties */
.section-title{width:1200px;left:0;text-align:center;font:700 42px 'Montserrat',sans-serif}
.spec-card{top:1443px;width:201px;height:270px;border:1.5px solid rgba(255,255,255,.8);text-align:center;color:var(--white)}
.spec-card svg{margin-top:28px}
.spec-card h3{font:600 16px 'Montserrat',sans-serif;margin-top:10px;line-height:19px}
.spec-card p{font-size:12.5px;line-height:18px;margin:10px 14px 0;opacity:.95}
.spec-card .arrow{position:absolute;left:88px;bottom:18px}

/* stats */
.stat{top:1945px;width:240px;text-align:center;color:var(--white)}
.stat .num{font:500 44px 'Montserrat',sans-serif;color:var(--orange);margin-top:8px;line-height:54px}
.stat .label{font-size:21px}

/* projects */
.project{background:linear-gradient(160deg,#9fb4d6,#6a7c6a)}

/* clients */
.client-card{top:3335px;width:409px;height:195px;border:1.5px solid rgba(255,255,255,.85);color:var(--white)}
.avatar{position:absolute;left:18px;top:24px;width:86px;height:86px;border-radius:50%;border:3px solid var(--white)}
.quote{position:absolute;left:124px;top:22px;width:260px;font-style:italic;font-size:12px;line-height:23px}
.quote b{display:block;font:700 14px 'Montserrat',sans-serif;font-style:normal;margin-top:6px}

/* form */
.field{background:var(--white);border:1px solid #d8dadf;font-size:12px;color:#444;padding:12px 16px}

/* footer */
.site-footer{left:0;top:4225px;width:1200px;height:415px;background:var(--orange)}
.footer-brand{left:169px;top:4370px;display:flex;align-items:center;gap:12px;font:700 30px 'Montserrat',sans-serif;color:var(--white);letter-spacing:1px}
.footer-brand span.sq{width:36px;height:36px;background:var(--white)}
.f-col h4{font:700 15px 'Montserrat',sans-serif;color:var(--white);margin-bottom:14px}
.f-col p{font-size:13px;line-height:21px;color:var(--white)}
.social{top:4592px;width:18px;height:18px;border-radius:50%;background:var(--white)}
</style>
</head>
<body>

<header class="abs site-header">
  <div class="abs brand"><span class="brand-mark"></span>SUMMIT BUILDERS</div>
  <div class="abs license-top">CSLB License # 2418596</div>
  <div class="abs email-top">
    <svg width="16" height="12" viewBox="0 0 16 12"><rect x="0.5" y="0.5" width="15" height="11" fill="none" stroke="#ef5a22"/><path d="M1 1l7 6 7-6" fill="none" stroke="#ef5a22"/></svg>
    info@summitbuildersca.example
  </div>
  <nav class="main-nav">
    <a class="active" style="left:398px">HOME</a>
    <a style="left:506px">ABOUT US</a>
    <a style="left:647px">SERVICES</a>
    <a style="left:784px">PROJECTS</a>
    <a style="left:924px">CONTACT US</a>
  </nav>
</header>

<section class="abs hero" role="img" aria-label="Glass office tower photographed against a dusk sky" style="background:linear-gradient(180deg,#8ea2bf 0%,#6d7b93 40%,#3d4656 75%,#c79f7e 100%)"></section>
<svg class="abs" style="left:0;top:580px" width="1200" height="130"><polygon points="0,5 595,125 1200,5 1200,130 0,130" fill="#fff"/></svg>
<svg class="abs" style="left:46px;top:360px" width="24" height="40"><path d="M20 2L4 20l16 18" fill="none" stroke="#fff" stroke-width="2"/></svg>
<svg class="abs" style="left:1143px;top:360px" width="24" height="40"><path d="M4 2l16 18L4 38" fill="none" stroke="#fff" stroke-width="2"/></svg>
<div class="abs hero-title">THE BEST CHOOSE US</div>
<div class="abs hero-sub">BECAUSE WE DELIVER</div>
<div class="abs btn hero-btn">READ MORE</div>

<section>
  <h1 class="abs welcome-title">Welcome!</h1>
  <p class="abs welcome-text">Sed ut perspiciatis unde omnis iste natus error sit voluptatem accusantium doloremque laudantium, totam rem aperiam, eaque ipsa quae ab illo inventore veritatis et quasi architecto beatae vitae dicta sunt explicabo. Nemo enim ipsam voluptatem quia voluptas sit aspernatur aut odit aut fugit, sed quia consequuntur magni dolores eos qui ratione voluptatem sequi nesciunt. Neque porro quisquam est, qui dolorem ipsum quia dolor sit amet, consectetur, adipisci velit, sed quia non numquam eius modi tempora incidunt ut labore et dolore magnam aliquam quaerat voluptatem ut enim ad minima veniam.</p>
  <svg class="abs" style="left:665px;top:834px" width="345" height="380" role="img" aria-label="Construction workers in hard hats framed inside a house outline">
    <defs><linearGradient id="crew" x1="0" y1="0" x2="0" y2="1"><stop offset="0" stop-color="#d9c8b2"/><stop offset=".5" stop-color="#8a8478"/><stop offset="1" stop-color="#5b5750"/></linearGradient></defs>
    <polygon points="0,110 172,0 345,110 345,380 0,380" fill="url(#crew)"/>
  </svg>
</section>

<section>
  <div class="abs" role="img" aria-label="Construction site photo tinted orange" style="left:0;top:1297px;width:1200px;height:517px;background:linear-gradient(120deg,var(--orange-deep),var(--orange) 50%,var(--orange-light))"></div>
  <h2 class="abs section-title" style="top:1352px;color:var(--white)">We Specializes</h2>

  <div class="abs spec-card" style="left:171px">
    <svg width="60" height="60" viewBox="0 0 60 60" fill="none" stroke="#fff" stroke-width="2"><path d="M6 28L26 10l20 18M10 25v26h24"/><rect x="18" y="34" width="8" height="10"/><path d="M46 34c-6 8-8 11-8 15a8 8 0 0016 0c0-4-2-7-8-15z"/></svg>
    <h3>Water and<br>Fire Damage</h3>
    <p>Sed ut perspiciatis undem nis iste natus error sit volupt atem aSed ut perspiciatis un de omnis iste natusr sit</p>
    <svg class="arrow" width="24" height="8"><path d="M0 4h22M18 1l4 3-4 3" stroke="#fff" fill="none"/></svg>
  </div>
  <div class="abs spec-card" style="left:389px">
    <svg width="60" height="60" viewBox="0 0 60 60" fill="none" stroke="#fff" stroke-width="2"><path d="M8 20h44L46 8H14z"/><rect x="10" y="20" width="40" height="34"/><rect x="16" y="26" width="8" height="8"/><rect x="36" y="26" width="8" height="8"/><rect x="26" y="38" width="8" height="16"/></svg>
    <h3>Residential<br>ReModels</h3>
    <p>Sed ut perspiciatis undem nis iste natus error sit volupt atem aSed ut perspiciatis un de omnis iste natusr sit</p>
    <svg class="arrow" width="24" height="8"><path d="M0 4h22M18 1l4 3-4 3" stroke="#fff" fill="none"/></svg>
  </div>
  <div class="abs spec-card" style="left:607px">
    <svg width="60" height="60" viewBox="0 0 60 60" fill="none" stroke="#fff" stroke-width="2"><path d="M4 52l18-28 10 14 8-10 16 24z"/><path d="M22 10c2-4 10-4 12 0 4-1 6 3 3 5H20c-3-1-2-5 2-5z"/></svg>
    <h3>Landscaping</h3>
    <p style="margin-top:19px">Sed ut perspiciatis undem nis iste natus error sit volupt atem aSed ut perspiciatis un de omnis iste natusr sit</p>
    <svg class="arrow" width="24" height="8"><path d="M0 4h22M18 1l4 3-4 3" stroke="#fff" fill="none"/></svg>
  </div>
  <div class="abs spec-card" style="left:825px">
    <svg width="60" height="60" viewBox="0 0 60 60" fill="none" stroke="#fff" stroke-width="2"><rect x="10" y="6" width="26" height="48"/><rect x="36" y="24" width="16" height="30"/><path d="M16 13h4M26 13h4M16 22h4M26 22h4M16 31h4M26 31h4M16 40h4M26 40h4M41 32h6M41 41h6"/></svg>
    <h3>Building ADU</h3>
    <p style="margin-top:19px">Sed ut perspiciatis undem nis iste natus error sit volupt atem aSed ut perspiciatis un de omnis iste natusr sit</p>
    <svg class="arrow" width="24" height="8"><path d="M0 4h22M18 1l4 3-4 3" stroke="#fff" fill="none"/></svg>
  </div>
</section>

<section>
  <div class="abs" role="img" aria-label="Business handshake photo in dark tones" style="left:0;top:1814px;width:1200px;height:466px;background:radial-gradient(ellipse at 55% 55%,#6b6560,#45474d 55%,#33353a)"></div>
  <svg class="abs" style="left:0;top:2225px" width="1200" height="56"><polygon points="0,56 0,56 640,32 1200,8 1200,56" fill="#fff"/><polygon points="640,32 1200,0 1200,28 780,32" fill="#ef5a22"/></svg>

  <div class="abs stat" style="left:132px">
    <svg width="44" height="40" viewBox="0 0 44 40"><path d="M22 2L2 20h6v18h10V26h8v12h10V20h6z" fill="#fff"/></svg>
    <div class="num">53</div><div class="label">Total Projects</div>
  </div>
  <div class="abs stat" style="left:348px">
    <svg width="56" height="40" viewBox="0 0 56 40" fill="#fff"><circle cx="28" cy="9" r="8"/><circle cx="12" cy="13" r="6"/><circle cx="44" cy="13" r="6"/><path d="M14 40c0-12 6-20 14-20s14 8 14 20z"/><path d="M0 38c0-10 5-16 12-16 3 0 5 1 6 2-3 4-5 9-5 14z"/><path d="M56 38c0-10-5-16-12-16-3 0-5 1-6 2 3 4 5 9 5 14z"/></svg>
    <div class="num">371</div><div class="label">Staff Members</div>
  </div>
  <div class="abs stat" style="left:590px">
    <svg width="42" height="42" viewBox="0 0 42 42"><circle cx="21" cy="21" r="19" fill="#fff"/><path d="M12 10c4 2 6 6 4 9s-6 2-6 6 4 4 4 8M26 6c-2 4 2 6 6 6M28 26c2 4 6 2 8 0" stroke="#45474d" stroke-width="3" fill="none"/></svg>
    <div class="num">15</div><div class="label">Working in States</div>
  </div>
  <div class="abs stat" style="left:817px">
    <svg width="42" height="42" viewBox="0 0 42 42"><circle cx="21" cy="21" r="18" fill="none" stroke="#fff" stroke-width="4"/><path d="M21 10v12h8" stroke="#fff" stroke-width="3" fill="none"/></svg>
    <div class="num">2,600</div><div class="label">Hours for Work</div>
  </div>
</section>

<section>
  <h2 class="abs section-title" style="top:2348px;color:var(--ink)">Recent Projects</h2>
  <div class="abs project" role="img" aria-label="Two-storey suburban home at dusk" style="left:173px;top:2449px;width:420px;height:281px;background:linear-gradient(180deg,#9aa8d8,#7b6f8d 55%,#566a4a)"></div>
  <div class="abs project" role="img" aria-label="School building with glass facade" style="left:600px;top:2449px;width:211px;height:239px;background:linear-gradient(160deg,#7fa8d6,#c9b896 55%,#6b7c8c)"></div>
  <div class="abs project" role="img" aria-label="White clapboard house under blue sky" style="left:818px;top:2449px;width:209px;height:239px;background:linear-gradient(180deg,#5d93d6,#e4e8ee 55%,#6f8e55)"></div>
  <div class="abs project" role="img" aria-label="Yellow villa with garden and pond" style="left:173px;top:2739px;width:420px;height:279px;background:linear-gradient(180deg,#c9e2f0,#8bb54a 50%,#2f7fb7)"></div>
  <div class="abs project" role="img" aria-label="Brick family home with double garage" style="left:600px;top:2695px;width:427px;height:323px;background:linear-gradient(180deg,#7fb0e8,#9a6250 50%,#7b8b6a)"></div>
</section>

<section>
  <svg class="abs" style="left:0;top:3115px" width="1200" height="580">
    <polygon points="0,10 1200,10 1200,60" fill="#4a4d55"/>
    <polygon points="0,10 1200,60 1200,516 0,560" fill="#ef5a22"/>
    <polygon points="0,560 1200,516 1200,580 0,580" fill="#4a4d55"/>
  </svg>
  <h2 class="abs section-title" style="top:3238px;color:var(--white)">Our Clients</h2>

  <div class="abs client-card" style="left:171px">
    <div class="avatar" role="img" aria-label="Client portrait" style="background:#c8a58a"></div>
    <p class="quote">"...and for all the wonderful work you and your crew are doing. Our team has nothing but good things to say - we are really fortunate to have found you for this project!"<b>- Daniel Reyes</b></p>
    <svg class="abs" style="left:340px;top:135px" width="42" height="34" viewBox="0 0 42 34" fill="#fff"><path d="M2 2h16v14c0 10-6 16-14 18v-6c4-2 6-5 6-8H2zM24 2h16v14c0 10-6 16-14 18v-6c4-2 6-5 6-8h-8z"/></svg>
  </div>
  <div class="abs client-card" style="left:616px">
    <div class="avatar" role="img" aria-label="Client portrait" style="background:#9c7f74"></div>
    <p class="quote">SummitBuilders is one of the best general contractors we've worked with. The entire team tactfully delivered a project of exceptional quality while staying<b>- Lena Park</b></p>
    <svg class="abs" style="left:340px;top:135px" width="42" height="34" viewBox="0 0 42 34" fill="#fff"><path d="M2 2h16v14c0 10-6 16-14 18v-6c4-2 6-5 6-8H2zM24 2h16v14c0 10-6 16-14 18v-6c4-2 6-5 6-8h-8z"/></svg>
  </div>
</section>

<section>
  <div class="abs" role="img" aria-label="Faded city skyline photo" style="left:0;top:3678px;width:1200px;height:547px;background:linear-gradient(180deg,#f4f5f7,#e4e6ea 70%,#d6d9de)"></div>
  <h2 class="abs section-title" style="top:3780px;color:var(--ink)">Request Quote</h2>
  <p class="abs" style="left:0;top:3856px;width:1200px;text-align:center;font-size:13px;line-height:22px;color:var(--body)">Sed ut perspiciatis unde omnis iste natus error sit voluptatem<br>accusantium doloremque laudantium, totam rem aper</p>
  <div class="abs field" style="left:331px;top:3926px;width:263px;height:38px">Name:</div>
  <div class="abs field" style="left:605px;top:3926px;width:262px;height:38px">Phone:</div>
  <div class="abs field" style="left:331px;top:3978px;width:263px;height:38px">Email:</div>
  <div class="abs field" style="left:605px;top:3978px;width:262px;height:38px">Subject:</div>
  <div class="abs field" style="left:331px;top:4029px;width:536px;height:79px">Message:</div>
  <div class="abs btn" style="left:542px;top:4126px;width:116px;height:40px;font-size:14px">SUBMIT</div>
</section>

<footer class="abs site-footer"></footer>
<div class="abs footer-brand"><span class="sq"></span>SUMMIT BUILDERS</div>
<div class="abs f-col" style="left:458px;top:4306px;width:260px">
  <h4>WORKING HOURS</h4>
  <p>We work 7 days a week, every day excluding major holidays. Contact us if you have an emergency, with our Hotline and Contact form.</p>
  <p style="margin-top:16px">Monday – Friday:10:00 – 16:00<br>Saturday:12:00 – 15:00<br>Sunday and holidays:09:00 – 12:00</p>
</div>
<div class="abs f-col" style="left:771px;top:4306px;width:300px">
  <h4>CONTACT US</h4>
  <p>Marcus T Hale | Branch Manager<br>Office : 555-014-2231<br>Direct : 555-018-7740<br>Fax : 555-019-3362<br>info@summitbuildersca.example<br>412 Cedar Ridge Ave Fairview, CA 90000</p>
</div>
<div class="abs social" style="left:171px"></div>
<div class="abs social" style="left:218px"></div>
<div class="abs social" style="left:265px"></div>
<div class="abs social" style="left:312px"></div>
<div class="abs" style="left:458px;top:4594px;font-size:12px;color:var(--white)">© 2020 Summit Builders. All rights reserved.</div>
<div class="abs" style="left:831px;top:4592px;font:700 15px 'Montserrat',sans-serif;color:var(--white)">CSLB License # 2418596</div>

</body>
</html>
```